Web Design for a Biotech Consulting Firm

We need a web site design for a new business based in Philadelphia called Verantel Dx. This is a consulting firm that will serve medical diagnostics industry, which is part of the life science/healthcare industry focusing on developing and marketing products that help in early detection, monitoring or management of diseases. Our consulting firm will help medical diagnostic companies to overcome key challenges in designing, evaluating and marketing new products.Our company name is Verantel Dx. Verantel is Latin word for "something" Dx represents diagnostics. The idea behind the name is that we help companies to transform the original, early product ideas ("nothing") into "something"; which is a product with full clinical utility that will help to improve health and well-being.The web site should use the visual feel of the logo (attached), be modern, simple and clean looking and represent creativity, innovation, scientific thinking and progress.
Updates

Wix Design is acceptable

Industry/Entity Type

Biotechnology

Coding

Coded - Design and coding required

Number of Pages Required

1 page

Font styles to use
Sans Serif

Requirements
Must have
• simple, clean look couple of pages
Should not have
• a lot of pages

```html
<!DOCTYPE html>
<html lang="en">
<head>
<meta charset="utf-8">
<title>Verantel Dx — Biotech Consulting</title>
<link href="https://fonts.googleapis.com/css2?family=Mulish:wght@300;400;600;700&display=swap" rel="stylesheet">
<style>
:root{
  --blue:#3b78c8;
  --ink:#1d1d1f;
  --muted:#555b66;
  --pale:#eef3fa;
  --white:#ffffff;
}
*{margin:0;padding:0;box-sizing:border-box}
html,body{width:1200px;height:3457px;overflow:hidden}
body{font-family:"Mulish",Arial,sans-serif;color:var(--ink);background:var(--white);position:relative}
.abs{position:absolute}
.accent{color:var(--blue)}
.btn{position:absolute;display:flex;align-items:center;justify-content:center;border:1.5px solid var(--blue);font-size:15px;color:var(--muted);background:transparent}
.btn svg{position:absolute;right:-18px;top:50%;transform:translateY(-50%)}

/* header */
.site-header{top:0;left:0;width:1200px;height:98px;border-bottom:1px solid #e6eaf0}
.brand{display:flex;align-items:center;gap:9px;font-size:17px;font-weight:600;color:var(--ink);white-space:nowrap}
.brand i{display:block;width:9px;height:9px;background:var(--blue)}
.site-header .brand{left:141px;top:36px}
.nav{top:38px;font-size:14px;color:var(--muted)}
.nav.active{color:var(--ink);font-weight:700;border:1.5px solid var(--blue);border-right:none;border-bottom:none;padding:2px 0 0 7px;top:35px}
.phone-icon{left:935px;top:34px}
.phone-label{left:968px;top:32px;font-size:12px;color:var(--muted);line-height:17px}

/* hero */
.hero{top:98px;left:0;width:1200px;height:544px;background:linear-gradient(90deg,#e6eff8 0%,#dde9f6 40%,#b9d1ea 70%,#8fb5de 100%)}
.hero-text{left:143px;top:271px;font-size:36px;line-height:46px;font-weight:600;letter-spacing:.5px}
.hero-text .dark{color:#222}
.dots{left:141px;top:591px;display:flex;gap:11px}
.dots i{width:13px;height:13px;border:1.5px solid var(--blue);display:block}
.dots i.on{background:var(--blue)}

/* challenges */
.challenges-title{top:726px;width:1200px;text-align:center;font-size:29px;font-weight:600}
.challenges-sub{top:768px;width:1200px;text-align:center;font-size:28px;color:var(--blue);font-weight:400}
.card{top:856px;height:206px;border:1.5px solid #555;background:var(--white);text-align:center}
.card.hl{border-color:var(--blue)}
.card h3{position:absolute;top:94px;width:100%;font-size:19px;font-weight:400}
.card p{position:absolute;top:128px;left:24px;right:24px;font-size:12px;line-height:16px;color:var(--muted)}
.card .icon{position:absolute;top:18px;left:50%;transform:translateX(-50%)}
.card .pin{position:absolute;left:-2px;top:28px;width:6px;height:6px;background:#555}
.num{top:882px;width:70px;text-align:right;font-size:118px;font-weight:300;color:transparent;-webkit-text-stroke:1.5px #555;line-height:1}
.num.hl{-webkit-text-stroke-color:var(--blue)}

/* about */
.about{top:1234px;left:0;width:1200px;height:437px;background:linear-gradient(120deg,#3d7fd0 0%,#5d97dc 45%,#4582cf 75%,#3670c2 100%);color:var(--white);text-align:center}
.about h2{position:absolute;top:86px;width:100%;font-size:29px;font-weight:600}
.about .rule{position:absolute;top:137px;left:565px;width:70px;height:1px;background:rgba(255,255,255,.7)}
.about .lead{position:absolute;top:160px;width:100%;font-size:15px;line-height:24px}
.about .body{position:absolute;top:221px;left:180px;width:840px;font-size:13.5px;line-height:21px}
.about .btn{border-color:var(--white);color:var(--white)}

/* asset */
.asset-photo{top:1671px;left:0;width:700px;height:435px;background:linear-gradient(100deg,#cfe0f0 0%,#e8f1f9 45%,#f4f7fb 75%,#ffffff 100%)}
.asset h2{position:absolute;left:722px;top:1830px;font-size:29px;font-weight:600}
.asset p{position:absolute;left:720px;top:1878px;width:360px;font-size:19px;line-height:29px;color:#333}

/* stats */
.stats{top:2106px;left:0;width:1200px;height:222px;background:var(--pale)}
.stat{top:75px;text-align:center}
.stat b{display:block;font-size:36px;font-weight:600;color:var(--blue);line-height:40px}
.stat span{display:block;font-size:16px;color:#222;margin-top:8px;font-weight:600}
.divider{top:68px;width:0;height:84px;border-left:1px dashed #9fb3cf}

/* news */
.news-photo{top:2328px;left:0;width:1200px;height:437px;background:linear-gradient(90deg,#f2f3f5 0%,#eceef1 45%,#c9ccd1 62%,#e8e4df 80%,#d9dde2 100%)}
.news h2{position:absolute;left:141px;top:2410px;font-size:29px;font-weight:600}
.news-item{left:143px;width:350px;font-size:14px;line-height:21px;color:#333}
.news-meta{left:143px;width:340px;font-size:14px;color:#333;display:flex;align-items:center}
.news-meta .more{margin-left:auto;font-weight:700;font-size:13px;display:flex;align-items:center;gap:6px}
.news-rule{left:141px;top:2576px;width:353px;border-top:1px dashed #9fb3cf}

/* contact */
.contact-title{top:2852px;width:1200px;text-align:center;font-size:29px;font-weight:600}
.contact-box{top:2928px;left:141px;width:918px;height:327px;background:#f7f9fc}
.contact-info{top:2928px;left:740px;width:319px;height:327px;background:var(--pale)}
.field{font-size:13px;color:var(--muted);border-bottom:1px dashed #9fb3cf;height:26px}
.info-row{left:776px;display:flex;gap:16px;font-size:14.5px;line-height:21px;color:#222}
.info-row .ico{width:38px;height:38px;border:1.5px solid var(--blue);display:flex;align-items:center;justify-content:center;background:var(--white);flex:none}

/* footer */
.site-footer .brand{left:178px;top:3348px;font-size:19px}
.foot-nav{top:3354px;left:352px;display:flex;align-items:center;gap:20px;font-size:13px;color:#333}
.foot-nav i{width:4px;height:4px;border-radius:50%;background:#9fb3cf;display:block}
.copyright{top:3356px;left:778px;font-size:13px;color:#333}
.bottom-bar{left:0;top:3453px;width:1200px;height:4px;background:var(--blue)}
</style>
</head>
<body>

<header class="abs site-header">
  <div class="abs brand"><i></i>Verantel Dx</div>
  <nav>
    <div class="abs nav active" style="left:530px">Home</div>
    <div class="abs nav" style="left:619px">About Us</div>
    <div class="abs nav" style="left:723px">Services</div>
    <div class="abs nav" style="left:821px">Contact Us</div>
  </nav>
  <div class="abs" style="left:916px;top:28px;width:1px;height:40px;background:#e0e5ec"></div>
  <svg class="abs phone-icon" width="24" height="24" viewBox="0 0 24 24" fill="none" stroke="#3b78c8" stroke-width="1.6"><circle cx="12" cy="12" r="11"/><path d="M8 6.5l2 3-1.2 1.2c.8 1.6 1.9 2.7 3.5 3.5L13.5 13l3 2-1.3 2c-4.5-.5-8.2-4.2-8.7-8.7z"/></svg>
  <div class="abs phone-label">PHONE<br>215-555-0148</div>
</header>

<section class="abs hero" role="img" aria-label="Laboratory scientists in white coats and safety glasses examining test tubes and taking notes"></section>
<div class="abs hero-text">
  <div class="accent">We Are</div>
  <div class="dark">A Biotech Consulting Firm</div>
  <div class="accent">Serving The Medical<br>Diagnostics Industry</div>
</div>
<div class="abs dots"><i class="on"></i><i></i><i></i><i></i></div>

<section>
  <h2 class="abs challenges-title">Our Consulting Firm Will Help Medical Diagnostic Companies</h2>
  <div class="abs challenges-sub">To Overcome Key Challenges In</div>

  <div class="abs num" style="left:128px">1</div>
  <div class="abs card" style="left:198px;width:224px">
    <i class="pin"></i>
    <svg class="icon" width="58" height="58" viewBox="0 0 58 58" fill="none" stroke="#444" stroke-width="1.5"><circle cx="18" cy="16" r="6"/><circle cx="40" cy="16" r="6"/><circle cx="12" cy="36" r="6"/><circle cx="29" cy="48" r="6"/><circle cx="46" cy="36" r="6"/><path d="M24 16h10M15 22l-2 8M18 40l6 5M35 46l7-6M44 22l1 8"/></svg>
    <h3>Designing</h3>
    <p>Lorem ipsum dolor sit amet, consectetuer adipiscing sed diam nonummy</p>
  </div>

  <div class="abs num hl" style="left:455px">2</div>
  <div class="abs card hl" style="left:525px;width:217px">
    <i class="pin" style="background:var(--blue)"></i>
    <svg class="icon" width="58" height="58" viewBox="0 0 58 58" fill="none" stroke="#3b78c8" stroke-width="1.5"><rect x="8" y="20" width="42" height="26"/><path d="M4 46h50v4H4z"/><circle cx="29" cy="14" r="9"/><path d="M29 8v6h5"/><path d="M14 40v-8M20 40v-12M26 40v-6M32 40v-10M38 40v-7M44 40v-11"/></svg>
    <h3>Market Analysis</h3>
    <p>Lorem ipsum dolor sit amet, consectetuer adipiscing sed diam nonummy</p>
  </div>

  <div class="abs num" style="left:777px">3</div>
  <div class="abs card" style="left:847px;width:211px">
    <i class="pin"></i>
    <svg class="icon" width="58" height="58" viewBox="0 0 58 58" fill="none" stroke="#444" stroke-width="1.5"><rect x="6" y="12" width="34" height="26"/><path d="M16 44h14M23 38v6"/><path d="M30 22l10-6v20l-10-6z"/><path d="M46 18l5-3M46 26h6M46 34l5 3"/><rect x="11" y="18" width="12" height="9"/><path d="M11 32h20"/></svg>
    <h3>Product Launch</h3>
    <p>Lorem ipsum dolor sit amet, consectetuer adipiscing sed diam nonummy</p>
  </div>

  <div class="btn" style="left:548px;top:1105px;width:96px;height:35px">Get Started
    <svg width="16" height="10" viewBox="0 0 16 10" fill="none" stroke="#3b78c8" stroke-width="1.3"><path d="M0 5h15M11 1l4 4-4 4"/></svg></div>
</section>

<section class="abs about" role="img" aria-label="Blue science backdrop with DNA helix, hexagon pattern and a close-up eye">
  <h2>About Verantel Dx</h2>
  <div class="rule"></div>
  <p class="lead">Verantel Dx This Is A Consulting Firm That Will Serve Medical Diagnostics Industry,<br>Which Is Part of The Life Science/healthcare Industry</p>
  <p class="body">Lorem ipsum dolor sit amet, consectetuer adipiscing elit, sed diam nonummy nibh euismod tincidunt ut laoreet dolore magna aliquam erat volutpat. Ut wisi enim ad minim veniam, quis nostrud exerci tation ullamcorper suscipit lobortis nisl ut aliquip ea commodo consequat. Duis autem vel eum iriure or sit amet, consectetuer adipiscing elit</p>
  <div class="btn" style="left:543px;top:310px;width:103px;height:35px">Read More
    <svg width="16" height="10" viewBox="0 0 16 10" fill="none" stroke="#fff" stroke-width="1.3"><path d="M0 5h15M11 1l4 4-4 4"/></svg></div>
</section>

<section class="asset">
  <div class="abs asset-photo" role="img" aria-label="Scientist with safety glasses holding a flask next to a microscope"></div>
  <h2>Asset <span class="accent">Partnering</span></h2>
  <p>Learn about our current partnering opportunities and submit your assets.</p>
  <div class="btn" style="left:720px;top:1956px;width:96px;height:35px">Learn More
    <svg width="16" height="10" viewBox="0 0 16 10" fill="none" stroke="#3b78c8" stroke-width="1.3"><path d="M0 5h15M11 1l4 4-4 4"/></svg></div>
</section>

<section class="abs stats">
  <div class="abs stat" style="left:132px;width:200px"><b>100</b><span>PROFESSIONAL STAFF</span></div>
  <div class="abs divider" style="left:381px"></div>
  <div class="abs stat" style="left:420px;width:100px"><b>50</b><span>ROOMS</span></div>
  <div class="abs divider" style="left:560px"></div>
  <div class="abs stat" style="left:606px;width:160px"><b>10</b><span>STARS COMFORT</span></div>
  <div class="abs divider" style="left:813px"></div>
  <div class="abs stat" style="left:860px;width:210px"><b>25</b><span>YEARS OF EXPERIENCE</span></div>
</section>

<section class="news">
  <div class="abs news-photo" role="img" aria-label="Smiling lab researcher and colleague working at a microscope"></div>
  <h2>Latest <span class="accent">News</span></h2>
  <p class="abs news-item" style="top:2470px">Lorem Quis nostrud exerci tation ullamcorper suscipit lobortis nisl ut aliquip ex ea commo</p>
  <div class="abs news-meta" style="top:2524px">
    <svg width="15" height="15" viewBox="0 0 15 15" fill="none" stroke="#3b78c8" stroke-width="1.3" style="margin-right:10px"><rect x="1" y="2.5" width="13" height="11"/><path d="M1 6h13M4 1v3M11 1v3"/></svg>June 17, 2019
    <span class="more">READ MORE <svg width="16" height="10" viewBox="0 0 16 10" fill="none" stroke="#3b78c8" stroke-width="1.3"><path d="M0 5h15M11 1l4 4-4 4"/></svg></span>
  </div>
  <div class="abs news-rule"></div>
  <p class="abs news-item" style="top:2605px">Lorem Quis nostrud exerci tation ullamcorper suscipit lobortis nisl ut aliquip ex ea commo</p>
  <div class="abs news-meta" style="top:2661px">
    <svg width="15" height="15" viewBox="0 0 15 15" fill="none" stroke="#3b78c8" stroke-width="1.3" style="margin-right:10px"><rect x="1" y="2.5" width="13" height="11"/><path d="M1 6h13M4 1v3M11 1v3"/></svg>June 17, 2019
    <span class="more">READ MORE <svg width="16" height="10" viewBox="0 0 16 10" fill="none" stroke="#3b78c8" stroke-width="1.3"><path d="M0 5h15M11 1l4 4-4 4"/></svg></span>
  </div>
</section>

<section>
  <h2 class="abs contact-title">CONTACT <span class="accent">US</span></h2>
  <div class="abs contact-box"></div>
  <div class="abs contact-info"></div>
  <div class="abs field" style="left:178px;top:2985px;width:234px">Name</div>
  <div class="abs field" style="left:442px;top:2985px;width:234px">Phone</div>
  <div class="abs field" style="left:178px;top:3039px;width:234px">Email</div>
  <div class="abs field" style="left:442px;top:3039px;width:234px">Company Name</div>
  <div class="abs field" style="left:178px;top:3093px;width:498px;height:48px">Message</div>
  <div class="btn" style="left:179px;top:3164px;width:96px;height:35px;color:#333">SUBMIT
    <svg width="16" height="10" viewBox="0 0 16 10" fill="none" stroke="#3b78c8" stroke-width="1.3"><path d="M0 5h15M11 1l4 4-4 4"/></svg></div>

  <div class="abs info-row" style="top:2972px">
    <span class="ico"><svg width="16" height="20" viewBox="0 0 16 20" fill="none" stroke="#3b78c8" stroke-width="1.6"><path d="M8 19s6-6.5 6-11A6 6 0 0 0 2 8c0 4.5 6 11 6 11z"/><circle cx="8" cy="8" r="2.2"/></svg></span>
    <span>Lorem Quis nostrud exercitionl<br>ullamcorper suscipit - 123 456</span></div>
  <div class="abs info-row" style="top:3049px">
    <span class="ico"><svg width="18" height="18" viewBox="0 0 24 24" fill="#3b78c8"><path d="M6.6 2l3 4.5-1.8 1.8c1.2 2.4 3 4.2 5.4 5.4l1.8-1.8 4.5 3-1.9 3.2C10.7 17.4 6.4 13.1 3.3 4z"/></svg></span>
    <span>CALL US :<br>215-555-0148</span></div>
  <div class="abs info-row" style="top:3127px">
    <span class="ico"><svg width="18" height="18" viewBox="0 0 24 24" fill="#3b78c8"><path d="M22 2L2 10l7 3 3 8z"/></svg></span>
    <span>EMAIL US:<br>info@verantel-dx.com</span></div>
</section>

<footer class="site-footer">
  <div class="abs brand"><i></i>Verantel Dx</div>
  <nav class="abs foot-nav"><span>Home</span><i></i><span>About Us</span><i></i><span>Services</span><i></i><span>Contact Us</span></nav>
  <div class="abs copyright">Copyright © 2019 Verantel Dx . All Rights Reserved.</div>
  <div class="abs bottom-bar"></div>
</footer>

</body>
</html>
```